Belmont Ridge Business Card Design Project

We have recently rebranded and would like to design new business cards that incorporate the corporate logo - double sided cards with corporate logo on one side and contact details on the other

Target Market(s)

Sophisticated and high net worth investors and finance industry professionals

Industry/Entity Type

Funds Management

Contact Information for Business Card

The card should prominently feature the company name and logo. Other details will be standard contact details for each staff member - name, address, phone, email, website

Colors
0054AA
0677BA
7BADD7
CADEEF
E8F1F8

Requirements
Must have
• Double-sided design with one side prominently featuring the corporate logo and the other side with all standard contact details

```html
<!DOCTYPE html>
<html lang="en">
<head>
<meta charset="utf-8">
<title>Belmont Ridge – Business Card</title>
<link rel="stylesheet" href="https://fonts.googleapis.com/css2?family=Jost:wght@400;500&family=Open+Sans:wght@400;700&display=swap">
<style>
  :root {
    --navy: #1f4472;
    --backdrop: #ababab;
    --paper: #ffffff;
    --ink-grey: #6e6e6e;
    --label-grey: #7a7a7a;
  }
  * { margin: 0; padding: 0; box-sizing: border-box; }
  html, body {
    width: 1200px;
    height: 1000px;
    overflow: hidden;
  }
  body {
    background: var(--backdrop);
    position: relative;
    font-family: "Open Sans", Arial, sans-serif;
  }
  .card {
    position: absolute;
    top: 250px;
    width: 297px;
    height: 515px;
  }
  .card--front {
    left: 263px;
    background: var(--navy);
  }
  .card--back {
    left: 625px;
    background: var(--paper);
  }
  .wordmark {
    font-family: "Jost", Arial, sans-serif;
    font-weight: 500;
    text-transform: uppercase;
    white-space: nowrap;
    display: flex;
    align-items: center;
  }
  .wordmark__dot {
    display: inline-block;
    border-radius: 50%;
  }
  .card--front .wordmark {
    position: absolute;
    left: 0;
    right: 0;
    top: 200px;
    justify-content: center;
    gap: 12px;
    color: var(--paper);
    font-size: 27px;
    letter-spacing: 1.5px;
  }
  .card--front .wordmark__dot {
    width: 14px;
    height: 14px;
    background: var(--paper);
  }
  .contact {
    position: absolute;
    left: 45px;
    top: 137px;
    right: 20px;
  }
  .contact__name {
    font-family: "Jost", Arial, sans-serif;
    font-weight: 500;
    font-size: 19px;
    letter-spacing: 1.6px;
    color: var(--navy);
    text-transform: uppercase;
    line-height: 1;
  }
  .contact__role {
    font-family: "Jost", Arial, sans-serif;
    font-weight: 500;
    font-size: 9.5px;
    letter-spacing: 1.3px;
    color: var(--label-grey);
    text-transform: uppercase;
    margin-top: 6px;
  }
  .contact__rule {
    width: 23px;
    height: 2px;
    background: var(--navy);
    margin-top: 7px;
  }
  .contact__lines {
    font-size: 14px;
    line-height: 17px;
    color: var(--ink-grey);
    margin-top: 24px;
    font-style: normal;
  }
  .contact__lines p + p { margin-top: 17px; }
  .contact__web { font-weight: 700; }
  .card--back .wordmark {
    position: absolute;
    left: 45px;
    top: 443px;
    gap: 8px;
    color: var(--navy);
    font-size: 17px;
    letter-spacing: 1px;
  }
  .card--back .wordmark__dot {
    width: 10px;
    height: 10px;
    background: var(--navy);
  }
</style>
</head>
<body>
  <section class="card card--front" aria-label="Card front">
    <div class="wordmark"><span class="wordmark__dot"></span>Belmont Ridge</div>
  </section>

  <section class="card card--back" aria-label="Card back">
    <div class="contact">
      <h1 class="contact__name">Daniel Whitcombe</h1>
      <div class="contact__role">Portfolio Manager</div>
      <div class="contact__rule"></div>
      <address class="contact__lines">
        <p>+02 9456 3170<br>clientdesk@belmont-ridge.com</p>
        <p>Level 14 Harbour Tower,<br>52 Kent Lane,<br>Sydney NSW 2000</p>
        <p class="contact__web">www.belmont-ridge.com</p>
      </address>
    </div>
    <div class="wordmark"><span class="wordmark__dot"></span>Belmont Ridge</div>
  </section>
</body>
</html>
```